Business Card for Industrial Distributor

We need a business card design for an industrial distributor. We sell machine parts for the manufacturing and oil industry. We would like the cards to look clean and modern but with a touch of industry.

Our colors are blue/white.

Please feel free to visit our website www.korvelpartsco.com

Target Market(s)

mexican manufacturers in the automobile/aerospace industry

Industry/Entity Type

Industrial

Colors
ffffff
0555a3

```html
<!DOCTYPE html>
<html lang="en">
<head>
<meta charset="utf-8">
<title>Korvel – Business Card</title>
<link rel="stylesheet" href="https://fonts.googleapis.com/css2?family=Source+Sans+3:wght@400;700&display=swap">
<style>
  :root {
    --stage: #000000;
    --card: #333438;
    --divider: #44464b;
    --ink: #ffffff;
    --accent: #1a6fc4;
    --brand: #2b3a9e;
    --brand-dot: #1f5fc0;
  }
  * { margin: 0; padding: 0; box-sizing: border-box; }
  html, body {
    width: 1200px; height: 900px; overflow: hidden;
    background: var(--stage);
    font-family: "Source Sans 3", "Helvetica Neue", Arial, sans-serif;
  }
  .stage { position: relative; width: 1200px; height: 900px; }
  .card {
    position: absolute; top: 271px;
    width: 457px; height: 281px;
    background: var(--card);
    border-radius: 14px;
  }
  .card--front { left: 137px; }
  .card--back { left: 626px; }

  .front-brand {
    position: absolute; left: 48px; top: 117px;
    display: flex; align-items: center; gap: 10px;
    color: var(--brand-dot);
    font-weight: 700; font-size: 36px; line-height: 1;
  }
  .brand-dot {
    width: 22px; height: 22px; border-radius: 50%;
    background: var(--brand-dot);
  }
  .divider {
    position: absolute; left: 211px; top: 78px;
    width: 1px; height: 130px; background: var(--divider);
  }
  .contact {
    position: absolute; left: 247px; top: 66px;
    color: var(--ink); font-size: 13.5px; line-height: 16.5px;
  }
  .contact__name { color: var(--accent); font-size: 19.5px; line-height: 22px; }
  .contact__role { margin-bottom: 11px; }
  .contact__address { margin-bottom: 10px; }
  .contact__list { list-style: none; }
  .contact__list li { display: flex; align-items: center; gap: 7px; margin-left: 1px; }
  .contact__list svg { width: 10px; height: 10px; flex: none; }

  .back-brand {
    position: absolute; left: 0; right: 0; top: 79px;
    display: flex; flex-direction: column; align-items: center; gap: 8px;
  }
  .back-brand .brand-dot { width: 70px; height: 70px; }
  .back-brand__name {
    color: var(--brand); font-weight: 700; font-size: 56px; line-height: 1;
    letter-spacing: 3px;
  }
</style>
</head>
<body>
<main class="stage">
  <section class="card card--front" aria-label="Card front">
    <div class="front-brand"><span class="brand-dot"></span>Korvel</div>
    <div class="divider"></div>
    <div class="contact">
      <p class="contact__name">Daniel Reyes</p>
      <p class="contact__role">Managing Director</p>
      <p class="contact__address">4820 Industrial Ave, Ste 12<br>Monterrey, NL 64000.</p>
      <ul class="contact__list">
        <li>
          <svg viewBox="0 0 10 10" aria-hidden="true"><path d="M2 1l2 2-1 1.3c.6 1.2 1.5 2.1 2.7 2.7L7 6l2 2-1.3 1.3C4.5 9 1 5.5.7 2.3z" fill="var(--accent)"/></svg>
          081-832 457 960
        </li>
        <li>
          <svg viewBox="0 0 10 10" aria-hidden="true"><rect x="0.5" y="2" width="9" height="6.5" fill="var(--accent)"/><path d="M0.5 2l4.5 3.5L9.5 2" stroke="var(--card)" stroke-width="0.9" fill="none"/></svg>
          info@korvelparts.com
        </li>
        <li>
          <svg viewBox="0 0 10 10" aria-hidden="true"><path d="M4 6l2-2M3.5 4.5L2 6a1.4 1.4 0 002 2l1.5-1.5M6.5 5.5L8 4a1.4 1.4 0 00-2-2L4.5 3.5" stroke="var(--accent)" stroke-width="1.1" fill="none" stroke-linecap="round"/></svg>
          www.korvelpartsco.com
        </li>
      </ul>
    </div>
  </section>

  <section class="card card--back" aria-label="Card back">
    <div class="back-brand">
      <span class="brand-dot"></span>
      <span class="back-brand__name">Korvel</span>
    </div>
  </section>
</main>
</body>
</html>
```